Verodex business card

Business card for sustainable investment company called "Verodex". Verodex is an exchange platform selling carbon credits between buyers and sellers. Carbon Credits are an environmental commodity for reducing global carbon emissions.

the card should obviously have our logo and the theme should be sustainability/environment mixed with a trading platform.

Contact Information for Business Card

Logo, Name, Title, Phone, Email

Colors
0054AA
0677BA
7BADD7
CADEEF
E8F1F8
0094D4
00A9DD
6FCCEA
C7EBF8
E9F6FB
00AB8E
00BBA5
67D7C9
C6EFE9
E9F9F6
59FF00
82FF00
B8FF75
E3FFCB
F4FFEA

```html
<!DOCTYPE html>
<html lang="en">
<head>
<meta charset="UTF-8">
<title>Verodex Business Card</title>
<link href="https://fonts.googleapis.com/css2?family=Montserrat:wght@400;500;700&display=swap" rel="stylesheet">
<style>
  :root {
    --bg: #e9eaec;
    --navy: #17294f;
    --sky: #33bde8;
    --aqua: #6fccea;
    --royal: #4368b5;
    --white: #ffffff;
    --ink: #1c1c1c;
  }
  * { margin: 0; padding: 0; box-sizing: border-box; }
  html, body { width: 1200px; height: 900px; overflow: hidden; }
  body {
    background: var(--bg);
    font-family: "Montserrat", sans-serif;
    position: relative;
  }
  .card {
    position: absolute;
    width: 630px;
    height: 360px;
    border-radius: 4px;
    box-shadow: 0 10px 26px rgba(0,0,0,0.16);
    overflow: hidden;
  }
  /* Front */
  .card-front {
    left: 120px; top: 60px;
    background: linear-gradient(30deg, #63c8df 0%, var(--sky) 40%, #3f9ad6 65%, var(--royal) 100%);
    display: flex; align-items: center; justify-content: center;
    gap: 20px;
  }
  .front-mark { width: 40px; height: 40px; background: var(--white); }
  .front-name {
    color: var(--white);
    font-weight: 700;
    font-size: 60px;
    letter-spacing: 3px;
  }
  /* Back */
  .card-back {
    left: 450px; top: 480px;
    background: var(--white);
  }
  .brand {
    position: absolute; left: 150px; top: 70px;
    display: flex; align-items: center; gap: 16px;
  }
  .brand-mark { width: 34px; height: 34px; background: linear-gradient(135deg, var(--aqua), var(--royal)); }
  .brand-name {
    color: var(--navy); font-weight: 700; font-size: 52px; letter-spacing: 2px;
  }
  .details {
    position: absolute; left: 120px; top: 160px;
    display: flex; align-items: center; gap: 22px;
  }
  .person { text-align: right; }
  .person-name { font-weight: 700; font-size: 22px; letter-spacing: 0.5px; }
  .person-first { color: var(--sky); }
  .person-last { color: var(--navy); }
  .person-title { font-size: 17px; color: var(--ink); margin-top: 2px; }
  .divider { width: 1.5px; height: 74px; background: var(--sky); }
  .contacts { list-style: none; font-size: 15px; color: var(--ink); }
  .contacts li { display: flex; align-items: center; gap: 10px; line-height: 24px; }
  .contacts svg { width: 16px; height: 16px; flex: none; }
  .footer { position: absolute; left: 0; bottom: 0; width: 630px; height: 80px; }
  .handle {
    position: absolute; right: 22px; bottom: 28px;
    color: var(--white); font-size: 20px;
  }
</style>
</head>
<body>
  <section class="card card-front">
    <span class="front-mark"></span>
    <span class="front-name">VERODEX</span>
  </section>

  <section class="card card-back">
    <div class="brand">
      <span class="brand-mark"></span>
      <span class="brand-name">VERODEX</span>
    </div>

    <div class="details">
      <div class="person">
        <div class="person-name"><span class="person-first">DANIEL</span> <span class="person-last">HARTWELL</span></div>
        <div class="person-title">Co-Founder</div>
      </div>
      <span class="divider"></span>
      <ul class="contacts">
        <li>
          <svg viewBox="0 0 16 16" aria-hidden="true"><path fill="#33bde8" d="M3.5 1.5l2.5 0 1 3.5-1.6 1.1a8 8 0 0 0 4.5 4.5L11 9l3.5 1v2.5c0 .8-.7 1.5-1.5 1.5A11.5 11.5 0 0 1 2 3c0-.8.7-1.5 1.5-1.5z"/></svg>
          555-210-4836
        </li>
        <li>
          <svg viewBox="0 0 16 16" aria-hidden="true"><rect x="1" y="3" width="14" height="10" rx="1" fill="#33bde8"/><path d="M1.5 3.8L8 9l6.5-5.2" fill="none" stroke="#fff" stroke-width="1.2"/></svg>
          info@verodex.com
        </li>
        <li>
          <svg viewBox="0 0 16 16" aria-hidden="true"><circle cx="8" cy="8" r="7" fill="#33bde8"/><path d="M1 8h14M8 1c-3 3.5-3 10.5 0 14M8 1c3 3.5 3 10.5 0 14" fill="none" stroke="#fff" stroke-width="0.9"/></svg>
          www.verodex.com
        </li>
      </ul>
    </div>

    <svg class="footer" viewBox="0 0 630 80" aria-hidden="true">
      <defs>
        <linearGradient id="tabFill" x1="0" y1="1" x2="1" y2="0">
          <stop offset="0" stop-color="#63c8df"/>
          <stop offset="0.5" stop-color="#38a6de"/>
          <stop offset="1" stop-color="#4368b5"/>
        </linearGradient>
      </defs>
      <rect x="0" y="38" width="440" height="5" fill="#33bde8"/>
      <rect x="0" y="50" width="440" height="30" fill="#17294f"/>
      <polygon points="452,0 630,0 630,80 452,80" fill="url(#tabFill)"/>
    </svg>
    <span class="handle">@verodex.com</span>
  </section>
</body>
</html>
```